Need wine label for brand that is named: Kesavati Vineyards & Winery

Kesavati is a yoga way of breathing. In Sanskrit Kesavati means "flying up." I would like a creative wine label that articulates Kesavati. The label should include a graphic and the name Kesavati on one line and Vineyards & Winery in smaller print underneath Kesavati.

```html
<!DOCTYPE html>
<html lang="en">
<head>
<meta charset="utf-8">
<title>Kesavati Vineyards &amp; Winery — Pinot Noir Label</title>
<link rel="stylesheet" href="https://fonts.googleapis.com/css2?family=Cinzel:wght@400&family=Cormorant+Garamond:wght@400;500;600&display=swap">
<style>
  :root {
    --crimson: #a3173e;
    --crimson-deep: #5e0f24;
    --ink: #333333;
    --paper: #ffffff;
    --ornament-grey: #d9d9d9;
    --ornament-soft: #f1f1f1;
  }
  * { margin: 0; padding: 0; box-sizing: border-box; }
  html, body { width: 943px; height: 1200px; overflow: hidden; background: var(--paper); }
  .label { position: relative; width: 943px; height: 1200px; background: var(--paper); overflow: hidden; }

  .band { position: absolute; left: 214px; width: 514px;
    background: linear-gradient(90deg, var(--crimson-deep), var(--crimson) 50%, var(--crimson-deep)); }
  .band--top { top: 0; height: 42px; }
  .band--bottom { bottom: 0; height: 44px; }

  .side-ornament { position: absolute; top: 248px; width: 188px; height: 712px; }
  .side-ornament--left { left: 24px; }
  .side-ornament--right { left: 732px; }

  .centre-medallion { position: absolute; left: 407px; top: 535px; width: 130px; height: 130px; }

  .text { position: absolute; left: 0; width: 943px; text-align: center; white-space: nowrap; }
  .brand-name { top: 84px; font-family: "Cormorant Garamond", serif; font-weight: 600;
    font-size: 96px; line-height: 1; color: var(--crimson); letter-spacing: 2px; }
  .brand-sub { top: 240px; font-family: "Cinzel", serif; font-size: 24px; letter-spacing: 4px; color: var(--ink); }
  .varietal { top: 378px; font-family: "Cormorant Garamond", serif; font-weight: 500;
    font-size: 82px; line-height: 1; color: var(--ink); }
  .vintage { top: 786px; font-family: "Cormorant Garamond", serif; font-size: 48px;
    letter-spacing: 12px; padding-left: 12px; color: var(--ink); line-height: 1; }
  .series { top: 868px; font-family: "Cinzel", serif; font-size: 50px; letter-spacing: 9px;
    padding-left: 9px; color: var(--ink); line-height: 1; }
  .region { top: 968px; font-family: "Cormorant Garamond", serif; font-size: 34px;
    color: var(--crimson); line-height: 1; }
  .abv { top: 1120px; font-family: "Cormorant Garamond", serif; font-size: 20px;
    letter-spacing: 4px; color: var(--ink); line-height: 1; }
</style>
</head>
<body>
<main class="label">
  <div class="band band--top"></div>

  <div class="text brand-name">Kesavati</div>
  <div class="text brand-sub">Vineyards &amp; Winery</div>

  <svg class="side-ornament side-ornament--left" viewBox="0 0 188 712" role="img" aria-label="Half mandala ornament with petal rings and red dots">
    <defs>
      <radialGradient id="orn-left" cx="1" cy="0.5" r="1">
        <stop offset="0" stop-color="var(--ornament-soft)"/>
        <stop offset="1" stop-color="var(--ornament-grey)"/>
      </radialGradient>
    </defs>
    <path d="M188 0 A188 356 0 0 0 188 712 Z" fill="url(#orn-left)"/>
  </svg>

  <svg class="side-ornament side-ornament--right" viewBox="0 0 188 712" role="img" aria-label="Half mandala ornament with petal rings and red dots">
    <defs>
      <radialGradient id="orn-right" cx="0" cy="0.5" r="1">
        <stop offset="0" stop-color="var(--ornament-soft)"/>
        <stop offset="1" stop-color="var(--ornament-grey)"/>
      </radialGradient>
    </defs>
    <path d="M0 0 A188 356 0 0 1 0 712 Z" fill="url(#orn-right)"/>
  </svg>

  <div class="text varietal">Pinot Noir</div>

  <svg class="centre-medallion" viewBox="0 0 130 130" role="img" aria-label="Crimson floral medallion ornament">
    <rect x="0" y="0" width="130" height="130" rx="14" fill="var(--crimson)"/>
  </svg>

  <div class="text vintage">2014</div>
  <div class="text series">COLLECTION</div>
  <div class="text region">Napa Valley</div>
  <div class="text abv">11.8% alc/vol.</div>

  <div class="band band--bottom"></div>
</main>
</body>
</html>
```